Need a stunning home page for Car rental company

For a client, I need a slick and sumber home page design. It is a small, local car rental company, with a handful of cars available for rent.
Selling points: affordable lease, availability, always clean cars
The design should be:
- flat and modern
- no, or very few animations/sliders
- CTA: booking form for renting a car.
- 3 featured cars with images and facts (see website) with button to read more about the car.
- fullscreen background video can be an option
- main colour: #efba01
The site is under construction here:
http://solvikutleie.hammerlia.no/
Delivery requirements:
I need a layered & well organised PSD file delivered.

```html
<!DOCTYPE html>
<html lang="en">
<head>
<meta charset="utf-8">
<title>Solvikutleie – Car Rental</title>
<link href="https://fonts.googleapis.com/css2?family=Roboto+Condensed:ital,wght@0,300;0,400;0,700;1,300;1,400&display=swap" rel="stylesheet">
<style>
:root{
  --gold:#efba01;
  --gold-soft:#e3b23c;
  --dark:#1f1f1f;
  --nav-active:#444;
  --panel:rgba(20,20,20,.82);
  --field:#8a8a8a;
  --grey-bg:#ebebeb;
  --text:#444;
  --muted:#888;
  --white:#fff;
}
*{box-sizing:border-box;margin:0;padding:0}
html,body{width:778px;height:1200px;overflow:hidden}
body{position:relative;font-family:"Roboto Condensed",Arial,sans-serif;font-weight:400;color:var(--text);background:var(--white)}
.abs{position:absolute}

/* header */
.site-header{position:absolute;left:0;top:0;width:778px;height:70px;background:var(--white)}
.brand{left:56px;top:20px;font-size:22px;font-weight:700;color:var(--gold);letter-spacing:1px}
.call{left:369px;top:17px;display:flex;align-items:center;gap:6px}
.call .label{font-size:10px;color:var(--muted);line-height:1}
.call .number{font-size:15px;color:var(--gold);line-height:1.1}
.search{left:555px;top:24px;width:167px;height:20px;border:1px solid #ccc;border-radius:2px;font-size:8px;color:#aaa;padding:5px 7px}
.search svg{position:absolute;right:6px;top:4px}

/* nav */
.main-nav{position:absolute;left:0;top:70px;width:778px;height:31px;background:var(--gold-soft);border-bottom:1px solid #c99b2c}
.main-nav ul{list-style:none;display:flex;position:absolute;left:55px;top:0;height:30px}
.main-nav li{font-size:8.5px;color:var(--white);line-height:30px;padding:0 15px}
.main-nav li.active{background:var(--nav-active);padding:0 19px}
.social{display:flex;gap:4px}
.social span{width:19px;height:19px;border-radius:50%;display:block}
.nav-social{left:632px;top:76px}
.nav-social span{background:#d8a42e;border:1px solid #c89526}

/* hero */
.hero{position:absolute;left:0;top:101px;width:778px;height:306px;background:linear-gradient(100deg,#f3a45e 0%,#c56b63 20%,#3a3035 45%,#1c1a1c 70%,#2a2627 100%)}
.slider-arrows{left:56px;top:239px;color:var(--white);font-size:24px;font-weight:300;letter-spacing:8px}
.booking{position:absolute;left:374px;top:101px;width:348px;height:306px;background:var(--panel)}
.booking h2{position:absolute;left:26px;top:30px;font-size:20px;font-weight:700;color:var(--white);letter-spacing:.3px}
.booking .row{position:absolute;left:0;width:348px;height:18px}
.booking label{position:absolute;right:224px;top:3px;font-size:9.5px;font-weight:400;color:#e6e6e6;white-space:nowrap;text-align:right}
.booking .field{position:absolute;left:143px;top:0;width:183px;height:18px;background:var(--field);border:1px solid #a4a4a4;font-size:7px;color:#bbb;padding:4px 9px}
.booking .field svg{position:absolute;right:5px;top:3px}
.booking .btn{position:absolute;left:143px;top:257px;width:183px;height:18px;background:var(--gold-soft);color:var(--white);font-size:8.5px;text-align:center;line-height:18px}

/* featured */
.featured{position:absolute;left:0;top:407px;width:778px;height:387px;background:var(--grey-bg)}
.featured h2{position:absolute;left:56px;top:24px;font-size:17px;font-weight:400;color:#555}
.featured .rule{position:absolute;left:56px;top:48px;width:666px;height:1px;background:#d8d8d8}
.car-card{position:absolute;top:61px;width:208px;height:303px;background:var(--white);box-shadow:0 8px 10px -8px rgba(0,0,0,.35)}
.car-photo{width:208px;height:123px}
.car-body{padding:10px 12px 0}
.car-name{font-size:10px;color:#444;padding-bottom:3px;border-bottom:1px solid #ddd}
.price{font-size:7px;color:var(--muted);margin-top:8px}
.price b{color:var(--gold);font-weight:400;font-size:8px;margin-left:4px}
.specs{margin-top:10px;font-size:6.8px;color:var(--muted);border-collapse:collapse}
.specs td{padding:0 0 3.6px 0;height:11.7px}
.specs td:first-child{width:80px}
.read-more{display:inline-block;margin-top:10px;background:var(--gold-soft);color:var(--white);font-size:8px;font-weight:400;padding:4px 12px}

/* welcome */
.welcome{position:absolute;left:0;top:794px;width:778px;height:132px;text-align:center}
.welcome h2{margin-top:33px;font-size:16px;font-weight:400;color:#444}
.welcome p{width:530px;margin:16px auto 0;font-size:8.6px;line-height:1.45;color:var(--muted);font-weight:300}

/* testimonials */
.testimonials{position:absolute;left:0;top:926px;width:778px;height:204px;background:var(--gold-soft)}
.testimonials h2{position:absolute;width:778px;top:32px;text-align:center;font-size:15px;font-weight:400;color:var(--white)}
.avatar{left:160px;top:73px;width:90px;height:90px;border-radius:50%;border:3px solid var(--white);background:linear-gradient(160deg,#d8d3cc,#7d7670)}
.quote{left:277px;top:90px;width:340px;color:var(--white);font-style:italic;font-size:8.6px;line-height:1.35;font-weight:300}
.quote .mark{position:absolute;left:-12px;top:-12px;font-size:14px}
.quote .author{margin-top:10px}
.t-arrow{top:106px;color:var(--white);font-size:20px}

/* footer */
.site-footer{position:absolute;left:0;top:1130px;width:778px;height:70px;background:var(--dark);color:#bbb;font-weight:400}
.site-footer .links{left:56px;top:19px;font-size:8px}
.site-footer .copy{left:56px;top:36px;font-size:8px}
.newsletter{left:273px;top:18px;font-size:8px}
.newsletter .input{position:absolute;left:0;top:15px;width:100px;height:16px;background:#333;color:#777;font-size:6.5px;padding:4px 7px}
.newsletter .sub{position:absolute;left:100px;top:15px;width:42px;height:16px;background:var(--gold-soft);color:var(--white);font-size:6.5px;text-align:center;line-height:16px}
.foot-call{left:467px;top:17px;display:flex;align-items:center;gap:5px}
.foot-call .label{font-size:7.5px;color:#888;line-height:1}
.foot-call .number{font-size:13px;color:#ccc;line-height:1.1}
.foot-social{left:634px;top:21px}
.foot-social span{background:#3a3a3a;border:1px solid #555}
</style>
</head>
<body>

<header class="site-header">
  <div class="abs brand">SOLVIKUTLEIE</div>
  <div class="abs call">
    <svg width="30" height="30" viewBox="0 0 30 30"><circle cx="15" cy="15" r="13.5" fill="none" stroke="#999" stroke-width="1.5"/><path d="M11 8c1 0 2.5 3 2.5 3.5S12 13 12 13.5s2.5 4 4.5 4.5c.5 0 1.5-1.5 2-1.5s3.5 1.5 3.5 2.5-1.5 3-3 3C14 22 8 16 8 11c0-1.5 2-3 3-3z" fill="#999"/></svg>
    <div><div class="label">Call Now</div><div class="number">1-800-555-0142</div></div>
  </div>
  <div class="abs search">Search
    <svg width="11" height="11" viewBox="0 0 11 11"><circle cx="4.5" cy="4.5" r="3.3" fill="none" stroke="#555" stroke-width="1.4"/><path d="M7 7l3 3" stroke="#555" stroke-width="1.6"/></svg>
  </div>
</header>

<nav class="main-nav">
  <ul>
    <li class="active">HOME</li><li>THE FLEET</li><li>OUR SERVICES</li><li>CONTACT US</li><li>BLOG</li><li>PAGE TEMPLATES</li><li>ABOUT US</li>
  </ul>
</nav>
<div class="abs social nav-social"><span></span><span></span><span></span><span></span></div>

<section class="hero" role="img" aria-label="Photo of a dark sedan on an open road at sunset"></section>
<div class="abs slider-arrows">‹ ›</div>

<form class="booking">
  <h2>BOOKING FORM</h2>
  <div class="row" style="top:71px"><label>PICK UP DATE</label><div class="field"><svg width="10" height="10" viewBox="0 0 10 10"><rect x=".5" y="1.5" width="9" height="8" fill="none" stroke="#ddd"/><path d="M.5 4h9M3 5.5h1M6 5.5h1M3 7.5h1M6 7.5h1" stroke="#ddd"/></svg></div></div>
  <div class="row" style="top:98px"><label>PICK UP TIME</label><div class="field">HH &nbsp;: &nbsp;MM</div></div>
  <div class="row" style="top:124px"><label>NUMBER OF PASSENGERS</label><div class="field"></div></div>
  <div class="row" style="top:151px"><label>PICKUP LOCATIONS</label><div class="field"></div></div>
  <div class="row" style="top:178px"><label>PHONE</label><div class="field"></div></div>
  <div class="row" style="top:204px"><label>EMAIL</label><div class="field"></div></div>
  <div class="row" style="top:231px"><label>SPECIAL REQUESTS</label><div class="field"></div></div>
  <div class="btn">BOOK NOW</div>
</form>

<section class="featured">
  <h2>FEATURED CARS</h2>
  <div class="rule"></div>

  <article class="car-card" style="left:56px">
    <div class="car-photo" role="img" aria-label="Photo of a black luxury coupe" style="background:linear-gradient(160deg,#9aa0a6,#3b3f44 60%,#22252a)"></div>
    <div class="car-body">
      <div class="car-name">Car Name</div>
      <div class="price">PRICE PER DAY <b>KR 600</b></div>
      <table class="specs">
        <tr><td>Biltype</td><td>Varebil</td></tr><tr><td>Maks. pers.</td><td>2</td></tr><tr><td>Ant. dører</td><td>5</td></tr><tr><td>Min. sjåføralder</td><td>21</td></tr><tr><td>Girtype</td><td>Manuell</td></tr><tr><td>Klimaanlegg?</td><td>Ja</td></tr><tr><td>Ubegrenset km?</td><td>Nei</td></tr>
      </table>
      <span class="read-more">Read More</span>
    </div>
  </article>

  <article class="car-card" style="left:285px">
    <div class="car-photo" role="img" aria-label="Photo of a red electric sedan, front view" style="background:radial-gradient(ellipse at 50% 60%,#c8262a 0%,#a51e22 35%,#efefef 70%)"></div>
    <div class="car-body">
      <div class="car-name">Car Name</div>
      <div class="price">PRICE PER DAY <b>KR 600</b></div>
      <table class="specs">
        <tr><td>Biltype</td><td>Varebil</td></tr><tr><td>Maks. pers.</td><td>2</td></tr><tr><td>Ant. dører</td><td>5</td></tr><tr><td>Min. sjåføralder</td><td>21</td></tr><tr><td>Girtype</td><td>Manuell</td></tr><tr><td>Klimaanlegg?</td><td>Ja</td></tr><tr><td>Ubegrenset km?</td><td>Nei</td></tr>
      </table>
      <span class="read-more">Read More</span>
    </div>
  </article>

  <article class="car-card" style="left:514px">
    <div class="car-photo" role="img" aria-label="Photo of a silver family sedan" style="background:radial-gradient(ellipse at 50% 55%,#b9bcc0 0%,#9ea2a7 35%,#e4e6e9 72%)"></div>
    <div class="car-body">
      <div class="car-name">Car Name</div>
      <div class="price">PRICE PER DAY <b>KR 600</b></div>
      <table class="specs">
        <tr><td>Biltype</td><td>Varebil</td></tr><tr><td>Maks. pers.</td><td>2</td></tr><tr><td>Ant. dører</td><td>5</td></tr><tr><td>Min. sjåføralder</td><td>21</td></tr><tr><td>Girtype</td><td>Manuell</td></tr><tr><td>Klimaanlegg?</td><td>Ja</td></tr><tr><td>Ubegrenset km?</td><td>Nei</td></tr>
      </table>
      <span class="read-more">Read More</span>
    </div>
  </article>
</section>

<section class="welcome">
  <h2>WELCOME SOLVIKBYEN CAR - STRANDVIK</h2>
  <p>Solvik car is a fleet of Strandvik and rent vans and cars for people who need a ekstrabil relocation, vacation, city tour or whatever. We beat the service, and most likely also the price. And you can trust that the car you get from us is both clean and pretty!</p>
</section>

<section class="testimonials">
  <h2>CLIENT TESTIMONIALS</h2>
  <div class="abs t-arrow" style="left:83px">‹</div>
  <div class="abs avatar" role="img" aria-label="Portrait photo of the client"></div>
  <blockquote class="abs quote">
    <span class="mark">“</span>
    Lorem ipsum dolor sit amet, consectetur adipisicing elit, sed do eiusmod tempor incididunt ut labore et dolore magna aliqua. Ut enim ad minim veniam, quis nostrud exercitation ullamco laboris nisi ut aliquip ex ea commodo consequat. Duis aute irure dolor in reprehenderit in voluptate velit esse cillum dolore eu fugiat nulla pariatur.
    <div class="author">- Henrik Dahl</div>
  </blockquote>
  <div class="abs t-arrow" style="left:680px">›</div>
</section>

<footer class="site-footer">
  <div class="abs links">About &nbsp;| &nbsp;Terms &nbsp;| &nbsp;Privacy Policy</div>
  <div class="abs copy">All Rights Reserved. Copyrights © 2014.</div>
  <div class="abs newsletter">Newsletter Signup
    <div class="input">Email Address</div><div class="sub">Subscribe</div>
  </div>
  <div class="abs foot-call">
    <svg width="26" height="26" viewBox="0 0 30 30"><circle cx="15" cy="15" r="13.5" fill="none" stroke="#888" stroke-width="1.5"/><path d="M11 8c1 0 2.5 3 2.5 3.5S12 13 12 13.5s2.5 4 4.5 4.5c.5 0 1.5-1.5 2-1.5s3.5 1.5 3.5 2.5-1.5 3-3 3C14 22 8 16 8 11c0-1.5 2-3 3-3z" fill="#888"/></svg>
    <div><div class="label">Call Us:</div><div class="number">040-5550-1234</div></div>
  </div>
  <div class="abs social foot-social"><span></span><span></span><span></span><span></span></div>
</footer>

</body>
</html>
```